Real Estate Cover Template

I am looking for a template design that I can use to post on IG and FB for my real estate closings and updates. The attachments shows examples...

Company name is Bright Harbor Realty and logo is attached.

Seeking:
Just Closed
Under Contract
New Listing
Just Sold
BH Agent

I am looking for something clean that has the company's logo, includes a picture of the subject home, includes sales price and includes our phone # (418-273-9046) and email contact@brightharbor.us.

Examples of competitors are provided for reference.

```html
<!DOCTYPE html>
<html lang="en">
<head>
<meta charset="utf-8">
<title>Bright Harbor Realty – Social Post Templates</title>
<link rel="stylesheet" href="https://fonts.googleapis.com/css2?family=Bebas+Neue&family=Oswald:wght@300;500&display=swap">
<style>
  :root{
    --brand-blue:#0d4fa8;
    --deep-blue:#1d3f86;
    --paper:#ffffff;
    --page:#ffffff;
    --sky-deep:#5f9bd8;
    --sky-pale:#b4d2ef;
    --stucco:#dcc29c;
    --stucco-deep:#c7a77f;
    --lawn:#6a9a48;
    --stone-warm:#b38a78;
    --stone-dark:#8f7569;
    --glass-light:#e2e8ee;
    --glass-mid:#b8c3ce;
  }
  *{box-sizing:border-box;margin:0;padding:0}
  html,body{width:1200px;height:789px;overflow:hidden;background:var(--page)}
  .sheet{position:relative;width:1200px;height:789px}
  .post{position:absolute;width:394px;height:389px;background:var(--paper);overflow:hidden}
  .col-1{left:0}.col-2{left:403px}.col-3{left:806px}
  .row-1{top:0}.row-2{top:400px}

  .photo{position:absolute}
  .photo-agent-warm{background:linear-gradient(160deg,var(--stone-warm) 0%,#c4937a 55%,var(--stone-dark) 100%)}
  .photo-agent-cool{background:linear-gradient(180deg,var(--glass-light) 0%,var(--glass-mid) 100%)}
  .photo-house{background:linear-gradient(180deg,var(--sky-deep) 0%,var(--sky-pale) 42%,var(--stucco) 62%,var(--stucco-deep) 80%,var(--lawn) 100%)}
  .photo-house-alt{background:linear-gradient(180deg,#79aee2 0%,#cfe1f2 40%,#ecdcb6 64%,#e3d0a6 80%,var(--lawn) 100%)}

  .band{position:absolute;left:0;width:394px;background:var(--brand-blue)}

  .brand{position:absolute;display:flex;flex-direction:column;align-items:center;justify-content:center;gap:5px;background:var(--paper);text-align:center}
  .brand-square{width:16px;height:16px;background:var(--brand-blue)}
  .brand-name{font-family:'Oswald',sans-serif;font-weight:500;color:var(--brand-blue);font-size:12.5px;line-height:1.1;text-transform:uppercase}

  .agent-name{position:absolute;font-family:'Bebas Neue',sans-serif;font-weight:400;color:var(--brand-blue);font-size:29px;line-height:1;white-space:nowrap}
  .contact{position:absolute;font-family:'Oswald',sans-serif;font-weight:300;color:var(--brand-blue);font-size:15px;line-height:1;display:flex;align-items:center;gap:8px;white-space:nowrap}
  .contact svg{width:14px;height:14px;fill:var(--brand-blue);flex:none}

  .headline{position:absolute;font-family:'Bebas Neue',sans-serif;font-weight:400;color:var(--brand-blue);line-height:.9;white-space:nowrap}
  .price{position:absolute;font-family:'Bebas Neue',sans-serif;color:var(--brand-blue);font-size:36px;line-height:1;white-space:nowrap}
  .specs{position:absolute;font-family:'Oswald',sans-serif;font-weight:300;color:var(--brand-blue);font-size:13.5px;line-height:1;white-space:nowrap}

  .contact-box{position:absolute;left:62px;top:351px;width:268px;height:23px;border:2px solid var(--brand-blue);display:flex;align-items:center;justify-content:space-evenly}
  .contact-box .contact{position:static;font-size:14px}
  .contact-box .contact svg{width:13px;height:13px}
</style>
</head>
<body>
<svg width="0" height="0" style="position:absolute">
  <symbol id="icon-phone" viewBox="0 0 24 24"><path d="M6.6 10.8a15.2 15.2 0 0 0 6.6 6.6l2.2-2.2c.3-.3.7-.4 1-.2 1.1.4 2.3.6 3.6.6.6 0 1 .4 1 1V20c0 .6-.4 1-1 1A17 17 0 0 1 3 4c0-.6.4-1 1-1h3.5c.6 0 1 .4 1 1 0 1.3.2 2.5.6 3.6.1.3 0 .7-.2 1z"/></symbol>
  <symbol id="icon-mail" viewBox="0 0 24 24"><path d="M2 4h20v16H2zm2 2v.5l8 5.5 8-5.5V6zm0 3v9h16V9l-8 5.5z"/></symbol>
</svg>

<main class="sheet">

  <section class="post col-1 row-1">
    <div class="photo photo-agent-warm" style="left:0;top:0;width:394px;height:295px" role="img" aria-label="Portrait photo of a smiling agent against a stone wall"></div>
    <div style="position:absolute;left:22px;top:262px;width:101px;height:104px;background:var(--brand-blue)"></div>
    <div class="brand" style="left:30px;top:270px;width:85px;height:88px"><span class="brand-square"></span><span class="brand-name">Bright Harbor<br>Realty</span></div>
    <div style="position:absolute;left:372px;top:296px;width:3px;height:22px;background:var(--brand-blue)"></div>
    <h2 class="agent-name" style="left:144px;top:302px">Name of Agent</h2>
    <p class="contact" style="left:146px;top:331px"><svg><use href="#icon-phone"/></svg>418-273-9046</p>
    <p class="contact" style="left:146px;top:347px"><svg><use href="#icon-mail"/></svg>contact@brightharbor.us</p>
  </section>

  <section class="post col-2 row-1">
    <div style="position:absolute;left:0;top:0;width:394px;height:302px;background:var(--deep-blue)"></div>
    <div class="photo photo-agent-cool" style="left:19px;top:18px;width:356px;height:284px" role="img" aria-label="Portrait photo of an agent in glasses and a dark jacket"></div>
    <div style="position:absolute;left:19px;top:276px;width:102px;height:96px;background:var(--brand-blue)"></div>
    <div class="brand" style="left:27px;top:276px;width:86px;height:86px"><span class="brand-square"></span><span class="brand-name">Bright Harbor<br>Realty</span></div>
    <h2 class="agent-name" style="left:142px;top:309px">Name of Agent</h2>
    <p class="contact" style="left:145px;top:336px"><svg><use href="#icon-phone"/></svg>418-273-9046</p>
    <p class="contact" style="left:145px;top:352px"><svg><use href="#icon-mail"/></svg>contact@brightharbor.us</p>
  </section>

  <section class="post col-3 row-1">
    <div class="band" style="top:48px;height:245px;clip-path:polygon(0 0,100% 12px,100% 100%,0 calc(100% - 14px))"></div>
    <div class="photo photo-house" style="left:0;top:51px;width:394px;height:224px;clip-path:polygon(0 0,100% 12px,100% 100%,0 calc(100% - 13px))" role="img" aria-label="Photo of a single-storey stucco home with a double garage and palm tree"></div>
    <div class="brand" style="left:155px;top:19px;width:86px;height:85px"><span class="brand-square"></span><span class="brand-name">Bright Harbor<br>Realty</span></div>
    <h1 class="headline" style="left:32px;top:300px;font-size:52px">New Listing</h1>
    <p class="price" style="left:256px;top:299px">$310,000</p>
    <p class="specs" style="left:254px;top:330px">4 BEDROOM 2.5 BATH</p>
    <div class="contact-box">
      <p class="contact"><svg><use href="#icon-phone"/></svg>418-273-9046</p>
      <p class="contact"><svg><use href="#icon-mail"/></svg>contact@brightharbor.us</p>
    </div>
  </section>

  <section class="post col-1 row-2">
    <p class="contact" style="right:32px;top:17px"><svg><use href="#icon-phone"/></svg>418-273-9046</p>
    <p class="contact" style="right:32px;top:36px"><svg><use href="#icon-mail"/></svg>contact@brightharbor.us</p>
    <div class="band" style="top:54px;height:256px;clip-path:polygon(0 0,100% 12px,100% 100%,0 calc(100% - 14px))"></div>
    <div class="photo photo-house" style="left:0;top:58px;width:394px;height:237px;clip-path:polygon(0 0,100% 12px,100% 100%,0 calc(100% - 13px))" role="img" aria-label="Photo of a single-storey stucco home with a double garage and palm tree"></div>
    <div class="brand" style="left:32px;top:22px;width:86px;height:80px"><span class="brand-square"></span><span class="brand-name">Bright Harbor<br>Realty</span></div>
    <h1 class="headline" style="left:30px;top:318px;font-size:60px">Just Sold</h1>
    <p class="price" style="left:254px;top:318px">$310,000</p>
    <p class="specs" style="left:254px;top:350px">4 BEDROOM 2.5 BATH</p>
  </section>

  <section class="post col-2 row-2">
    <p class="contact" style="right:32px;top:20px"><svg><use href="#icon-phone"/></svg>418-273-9046</p>
    <p class="contact" style="right:32px;top:39px"><svg><use href="#icon-mail"/></svg>contact@brightharbor.us</p>
    <div class="band" style="top:57px;height:256px;clip-path:polygon(0 0,100% 12px,100% 100%,0 calc(100% - 14px))"></div>
    <div class="photo photo-house" style="left:0;top:61px;width:394px;height:237px;clip-path:polygon(0 0,100% 12px,100% 100%,0 calc(100% - 13px))" role="img" aria-label="Photo of a single-storey stucco home with a double garage and palm tree"></div>
    <div class="brand" style="left:32px;top:25px;width:86px;height:80px"><span class="brand-square"></span><span class="brand-name">Bright Harbor<br>Realty</span></div>
    <h1 class="headline" style="left:26px;top:323px;font-size:57px">Just Closed</h1>
    <p class="price" style="left:266px;top:323px">$310,000</p>
    <p class="specs" style="left:266px;top:354px">4 BEDROOM 2.5 BATH</p>
  </section>

  <section class="post col-3 row-2">
    <div class="band" style="top:46px;height:250px;clip-path:polygon(0 0,100% 12px,100% 100%,0 calc(100% - 14px))"></div>
    <div class="photo photo-house-alt" style="left:0;top:49px;width:394px;height:231px;clip-path:polygon(0 0,100% 12px,100% 100%,0 calc(100% - 13px))" role="img" aria-label="Photo of a cream single-storey home with palms and a front lawn"></div>
    <div class="brand" style="left:159px;top:21px;width:86px;height:79px"><span class="brand-square"></span><span class="brand-name">Bright Harbor<br>Realty</span></div>
    <h1 class="headline" style="left:29px;top:300px;font-size:44px;line-height:.84">Under<br>Contract</h1>
    <p class="contact" style="right:28px;top:320px"><svg><use href="#icon-phone"/></svg>418-273-9046</p>
    <p class="contact" style="right:28px;top:341px"><svg><use href="#icon-mail"/></svg>contact@brightharbor.us</p>
  </section>

</main>
</body>
</html>
```